Business Card for Multi-Brand Sportswear Company

We are looking for a business card which represents our company and the multiple brands within it.

The company: Fen Athletics (LTD)
The brands: Fen, TavaPuni, ElmStretch, Grit and Rain

Employees using these cards would be representing Fen Athletics, rather than any of the individual brands. You will see a current design within the uploaded files, to give some inspiration. The actual text of the brands is not necessary, but the logos should be on there is some format.

Our creative minds on this are stretched, so we are looking for someone to make this their own, and show us what a good business card should look like.

We may like to get these printed with spot gloss, so keep that in mind with your designs.

www.fenathletics.co.uk

Industry/Entity Type

Business

Contact Information for Business Card

Leo Pemberton-Hale
Operations Manager
(+44) 1632 960 418
Leo@fenathletics.co.uk
www.fenathletics.co.uk

Font styles to use
Sans Serif
Other font styles liked:
• Eurostile

Colors
ffffff

Requirements
Nice to have
• Dark (black) background

```html
<!DOCTYPE html>
<html lang="en">
<head>
<meta charset="utf-8">
<title>Fen Athletics – Business Card</title>
<link rel="stylesheet" href="https://fonts.googleapis.com/css2?family=Michroma&family=Saira:wght@400;600&display=swap">
<style>
  :root {
    --ink: #1f1f21;
    --red: #b01e27;
    --paper: #ffffff;
    --backdrop: #e8e6e3;
    --muted: #4a4a4c;
  }
  * { box-sizing: border-box; margin: 0; padding: 0; }
  html, body { width: 1200px; height: 801px; overflow: hidden; }
  body {
    background: var(--backdrop);
    font-family: "Saira", sans-serif;
    position: relative;
  }
  .card {
    position: absolute;
    top: 232px;
    width: 520px;
    height: 336px;
    background: var(--paper);
    box-shadow: 0 8px 24px rgba(0,0,0,.18);
    overflow: hidden;
  }
  .card--front { left: 60px; }
  .card--back { left: 620px; }
  .card__bands { position: absolute; inset: 0; }

  /* Front */
  .brand-lockup { position: absolute; left: 70px; top: 96px; }
  .brand-name {
    font-family: "Michroma", sans-serif;
    font-size: 34px;
    letter-spacing: 1px;
    color: var(--ink);
    text-transform: uppercase;
    line-height: 1;
    white-space: nowrap;
  }
  .brand-tagline {
    font-family: "Saira", sans-serif;
    font-size: 14px;
    letter-spacing: 2px;
    color: var(--ink);
    text-transform: uppercase;
    text-align: right;
    margin-top: 8px;
  }
  .front-url {
    position: absolute;
    left: 26px;
    bottom: 52px;
    color: var(--paper);
    font-size: 14px;
    letter-spacing: .5px;
  }

  /* Back */
  .back-logo {
    position: absolute;
    right: 22px;
    top: 62px;
    text-align: right;
    color: var(--paper);
  }
  .back-logo .brand-name { font-size: 16px; letter-spacing: .5px; color: var(--paper); }
  .back-logo .brand-tagline { font-size: 8px; color: var(--paper); margin-top: 4px; letter-spacing: 1.5px; }
  .person { position: absolute; left: 24px; top: 70px; display: flex; align-items: center; gap: 10px; }
  .person__dot { width: 26px; height: 26px; border-radius: 50%; background: var(--red); flex: none; }
  .person__name {
    font-family: "Michroma", sans-serif;
    font-size: 11px;
    color: var(--ink);
    text-transform: uppercase;
    white-space: nowrap;
  }
  .person__role {
    font-size: 10px;
    letter-spacing: 1.5px;
    color: var(--muted);
    text-transform: uppercase;
    margin-top: 2px;
  }
  .contact {
    position: absolute;
    display: flex;
    flex-direction: column;
    align-items: center;
    gap: 6px;
    color: var(--paper);
    font-size: 12px;
    letter-spacing: .3px;
    white-space: nowrap;
  }
  .contact--phone { left: 20px; top: 168px; }
  .contact--email { left: 178px; top: 184px; }
  .contact--web { right: 20px; top: 200px; }
  .contact__icon {
    width: 26px; height: 26px; border-radius: 50%;
    background: var(--paper);
    display: flex; align-items: center; justify-content: center;
  }
  .brand-row {
    position: absolute;
    left: 16px;
    bottom: 22px;
    width: 280px;
    display: flex;
    justify-content: space-between;
    color: var(--paper);
    font-family: "Saira", sans-serif;
    font-weight: 600;
    font-size: 11px;
    letter-spacing: .5px;
  }
</style>
</head>
<body>

<section class="card card--front" aria-label="Card front">
  <svg class="card__bands" viewBox="0 0 520 336" aria-hidden="true">
    <path fill="var(--ink)" d="M0 0H520V88H322Q310 88 304 78L294 60Q288 52 276 52H0Z"/>
    <path fill="var(--red)" d="M0 186H520V336H0Z"/>
    <path fill="var(--paper)" d="M300 186H520V214H312Q304 214 300 206Z"/>
    <path fill="var(--ink)" d="M0 244H262Q274 244 280 256L288 280Q294 296 310 296H520V336H0Z"/>
  </svg>
  <div class="brand-lockup">
    <div class="brand-name">Fen Athletics</div>
    <div class="brand-tagline">Performance Wear</div>
  </div>
  <p class="front-url">www.fenathletics.co.uk</p>
</section>

<section class="card card--back" aria-label="Card back">
  <svg class="card__bands" viewBox="0 0 520 336" aria-hidden="true">
    <path fill="var(--ink)" d="M0 0H520V112H292Q280 112 274 102L264 70Q258 56 244 56H0Z"/>
    <path fill="var(--red)" d="M0 150H520V336H0Z"/>
    <path fill="var(--ink)" d="M0 256H300Q312 256 318 268L326 292Q332 306 346 306H520V336H0Z"/>
  </svg>

  <div class="back-logo">
    <div class="brand-name">Fen Athletics</div>
    <div class="brand-tagline">Performance Wear</div>
  </div>

  <div class="person">
    <span class="person__dot"></span>
    <div>
      <p class="person__name">Leo Pemberton-Hale</p>
      <p class="person__role">Operations Manager</p>
    </div>
  </div>

  <div class="contact contact--phone">
    <span class="contact__icon">
      <svg width="14" height="14" viewBox="0 0 24 24" aria-hidden="true"><path fill="var(--red)" d="M6.6 10.8a15 15 0 0 0 6.6 6.6l2.2-2.2a1 1 0 0 1 1-.25 11.4 11.4 0 0 0 3.6.57 1 1 0 0 1 1 1V20a1 1 0 0 1-1 1A17 17 0 0 1 3 4a1 1 0 0 1 1-1h3.5a1 1 0 0 1 1 1c0 1.25.2 2.45.57 3.57a1 1 0 0 1-.25 1z"/></svg>
    </span>
    <span>(+44) 1632 960 418</span>
  </div>

  <div class="contact contact--email">
    <span class="contact__icon">
      <svg width="14" height="14" viewBox="0 0 24 24" aria-hidden="true"><rect x="3" y="6" width="18" height="12" rx="1" fill="none" stroke="var(--red)" stroke-width="2"/><path d="M3 7l9 6 9-6" fill="none" stroke="var(--red)" stroke-width="2"/></svg>
    </span>
    <span>Leo@fenathletics.co.uk</span>
  </div>

  <div class="contact contact--web">
    <span class="contact__icon">
      <svg width="14" height="14" viewBox="0 0 24 24" aria-hidden="true"><g fill="none" stroke="var(--red)" stroke-width="2"><circle cx="12" cy="12" r="9"/><path d="M3 12h18M12 3c3 3 3 15 0 18M12 3c-3 3-3 15 0 18"/></g></svg>
    </span>
    <span>www.fenathletics.co.uk</span>
  </div>

  <div class="brand-row">
    <span>Fen</span>
    <span>TavaPuni</span>
    <span>ElmStretch</span>
    <span>Grit and Rain</span>
  </div>
</section>

</body>
</html>
```